A private security company called "Tavron Security Services Ltd"

Hello everybody,

We need a web page for a company based in NZ. It is mainly an informative website so it would be wonderful if the designer puts their absolute best into making it a website that I would really appreciate. The website needs to show professionalism and also needs to make our web surfers find the information they need in a click. the company's colour is black and silver, and if those two colours could be integrated into the website it would be absolutely lovely. Please do contact me for any information.

Sincerely,
Dorian Vaskel

Industry/Entity Type

Security

```html
<!DOCTYPE html>
<html lang="en">
<head>
<meta charset="utf-8">
<title>Tavron Security Services Ltd</title>
<link rel="stylesheet" href="https://fonts.googleapis.com/css2?family=Mulish:wght@400;600;700&family=Questrial&display=swap">
<style>
:root{
  --black:#000;
  --ink:#1a1a1a;
  --text:#555;
  --navy:#0d3f73;
  --link:#1a5aa8;
  --silver-hi:#ffffff;
  --silver-lo:#e6e6e6;
  --caption:rgba(22,72,130,.86);
  --line:#cfcfcf;
  --footer-text:#d8d8d8;
}
*{margin:0;padding:0;box-sizing:border-box}
html,body{width:1098px;height:1200px;overflow:hidden;background:#fff}
body{position:relative;font-family:"Mulish",sans-serif;color:var(--ink)}
.abs{position:absolute}

/* header */
.header{left:0;top:0;width:1098px;height:124px;background:linear-gradient(#fff,var(--silver-lo))}
.utility-bar{left:357px;top:0}
.utility-links{top:5px;left:0;width:1098px;font-size:11.5px;color:#fff}
.utility-links span{position:absolute;white-space:nowrap}
.brand{left:110px;top:34px;display:flex;align-items:center;gap:10px}
.brand-mark{width:26px;height:26px;border-radius:50%;background:var(--ink)}
.brand-name{font-size:15px;font-weight:700;color:var(--ink);line-height:1.25;width:150px}
.call{left:778px;top:50px;display:flex;align-items:center;gap:9px;font-size:18px;color:#333}
.call b{font-weight:400;color:var(--link)}
.nav-tab{left:366px;top:112px;z-index:2}
.nav{top:115px;left:0;width:1098px;height:0;font-size:13px;color:var(--link);z-index:3}
.nav span{position:absolute;transform:translateX(-50%);white-space:nowrap}
.nav i{position:absolute;top:-6px;width:1px;height:30px;background:var(--line)}

/* hero */
.hero{left:0;top:124px;width:1098px;height:377px;
  background:linear-gradient(90deg,#fbfdff 0%,#dde9f5 35%,#b7cce2 60%,#a8a8a4 82%,#9d978f 100%)}
.hero-title{left:111px;top:216px;font-family:"Questrial",sans-serif;font-size:37px;line-height:39px;color:#111;letter-spacing:.5px}
.hero-text{left:112px;top:298px;width:410px;font-size:12.5px;line-height:18.5px;color:#555}
.btn{left:112px;top:389px;width:103px;height:30px;border-radius:2px;background:linear-gradient(#4a4a4a,#111);color:#fff;font-size:12.5px;font-weight:600;display:flex;align-items:center;justify-content:center;letter-spacing:.3px}

/* ticker */
.ticker{left:105px;top:528px;width:893px;height:34px;border:1px solid var(--line);border-radius:4px;background:linear-gradient(#fff,#f0f0f0)}
.ticker-tab{left:124px;top:522px;width:138px;height:51px;background:#000;border-radius:6px 6px 0 0;clip-path:polygon(0 0,100% 0,100% 100%,50% 88%,0 100%);color:#fff;font-size:13.5px;font-weight:600;display:flex;justify-content:center;padding-top:15px}
.ticker-items{left:278px;top:539px;width:710px;overflow:hidden;font-size:11px;color:#333;white-space:nowrap;display:flex;gap:14px}
.ticker-items span::before{content:"";display:inline-block;width:6px;height:6px;border-radius:50%;background:#444;margin-right:11px;vertical-align:1px}

/* why */
.why-title{left:0;width:1098px;top:610px;text-align:center;font-family:"Questrial",sans-serif;font-size:26px;color:var(--navy);letter-spacing:.5px}
.why-text{left:125px;width:848px;top:655px;text-align:center;font-size:14.5px;line-height:23px;color:#555}
.card{top:729px;width:275px;height:147px;overflow:hidden}
.card .caption{position:absolute;left:0;bottom:0;width:100%;height:40px;background:var(--caption);color:#fff;font-size:18px;display:flex;align-items:center;justify-content:center}
.card-guards{left:119px;background:linear-gradient(90deg,#c8d3dc,#7f95b0 45%,#2d3550)}
.card-events{left:418px;background:linear-gradient(90deg,#5e6a55,#2c2f36 40%,#a9c24a 85%)}
.card-bodyguard{left:716px;background:linear-gradient(#b9bfc5,#6c7078 50%,#2a2b30)}
.arrow{top:788px}

/* footer */
.footer{left:0;top:922px;width:1098px;height:219px;background:#000}
.col{top:945px;color:var(--footer-text);font-size:11.5px;line-height:21px}
.col h3{color:#fff;font-size:14px;font-weight:600;margin-bottom:17px}
.social{left:754px;top:988px;display:flex;gap:6px}
.social span{width:29px;height:29px;border-radius:2px}
.footer-phone{left:754px;top:1030px;color:#fff;font-size:21px;font-weight:700;letter-spacing:.5px}
.search{left:754px;top:1071px;width:214px;height:29px;background:#fff;border:1px solid #bbb;font-size:11px;color:#999;padding:7px 11px}
.search svg{position:absolute;right:9px;top:7px}
.copyright{left:0;width:1098px;top:1160px;text-align:center;font-size:11px;color:#333}
</style>
</head>
<body>

<header class="header abs"></header>
<svg class="utility-bar abs" width="654" height="25" viewBox="0 0 654 25" aria-hidden="true">
  <path d="M0 0H654L632 21Q628 25 620 25H30Q24 25 20 21Z" fill="#000"/>
</svg>
<nav class="utility-links abs">
  <span style="left:661px">Security Services</span>
  <span style="left:770px">|</span>
  <span style="left:796px">News &amp; Events</span>
  <span style="left:892px">|</span>
  <span style="left:920px">Contact Us</span>
</nav>

<div class="brand abs">
  <span class="brand-mark"></span>
  <span class="brand-name">Tavron Security Services Ltd</span>
</div>

<div class="call abs">
  <svg width="31" height="31" viewBox="0 0 31 31" aria-hidden="true">
    <circle cx="15.5" cy="15.5" r="14" fill="none" stroke="#1a5aa8" stroke-width="2.2"/>
    <path d="M11 8.5l3 3-1.8 2.2q1.6 3.4 5 5.1l2.2-1.8 3 3-2 2.3q-4.8.2-8.6-3.6T8.7 10.5Z" fill="#1a5aa8"/>
  </svg>
  <span>CALL : <b>555-014-2290</b></span>
</div>

<section class="hero abs" role="img" aria-label="Wall-mounted CCTV security camera against a bright blue sky"></section>

<svg class="nav-tab abs" width="624" height="36" viewBox="0 0 624 36" aria-hidden="true">
  <defs><linearGradient id="tabFill" x1="0" y1="0" x2="0" y2="1"><stop offset="0" stop-color="#ececec"/><stop offset="1" stop-color="#fafafa"/></linearGradient></defs>
  <path d="M0 0Q10 0 20 18Q28 34 46 34H578Q596 34 604 18Q614 0 624 0Z" fill="url(#tabFill)"/>
</svg>
<nav class="nav abs">
  <span style="left:440px">Home</span>
  <i style="left:483px"></i>
  <span style="left:561px">Customer Services</span>
  <i style="left:632px"></i>
  <span style="left:712px">Security Services</span>
  <i style="left:793px"></i>
  <span style="left:874px">Why Tavron Security?</span>
</nav>

<h1 class="hero-title abs">WELCOME TO TAVRON<br>SECURITY SERVICES</h1>
<p class="hero-text abs">Lorem Ipsum is simply dummy text of the printing and typesetting industry. Lorem Ipsum has been the industry's standard dummy text ever since the 1500s, when an unknown printer took a galley of type and scrambled it to make a type specimen book. unchanged.</p>
<a class="btn abs">READ MORE</a>

<div class="ticker abs"></div>
<div class="ticker-tab abs">NEWS &amp; EVENTS</div>
<div class="ticker-items abs">
  <span>LOREM IPSUM DOLOR SIT AMET AND TYPESETTING INDUSTRY AND END</span>
  <span>LOREM IPSUM DOLOR SIT AMET AND TYPESETTIN</span>
</div>

<h2 class="why-title abs">WHY PEOPLE CHOOSE US</h2>
<p class="why-text abs">Lorem Ipsum is simply dummy text of the printing and typesetting industry. Lorem Ipsum has been the industry's standard dummy text ever since the 1500s, when an unknown printer took a galley of type and scrambled</p>

<svg class="arrow abs" style="left:95px" width="14" height="28" viewBox="0 0 14 28" aria-hidden="true"><path d="M12 2L3 14l9 12" fill="none" stroke="#222" stroke-width="2"/></svg>
<div class="card card-guards abs" role="img" aria-label="Uniformed property guard with belt and baton"><div class="caption">Property Guards</div></div>
<div class="card card-events abs" role="img" aria-label="Security officer at a crowded corporate event"><div class="caption">Corporate Events Security</div></div>
<div class="card card-bodyguard abs" role="img" aria-label="Bodyguards in suits escorting a black car"><div class="caption">Personal Bodyguard</div></div>
<svg class="arrow abs" style="left:1003px" width="14" height="28" viewBox="0 0 14 28" aria-hidden="true"><path d="M2 2l9 12-9 12" fill="none" stroke="#222" stroke-width="2"/></svg>

<footer class="footer abs"></footer>
<div class="col abs" style="left:125px">
  <h3>Services</h3>
  Property Guards<br>Event Security<br>Personal Bodyguard<br>Security Consultancy<br>Private Investigation
</div>
<div class="col abs" style="left:338px">
  <h3>Technical Center</h3>
  Installation<br>Drawings<br>Faqs<br>Documents
</div>
<div class="col abs" style="left:556px">
  <h3>About Us</h3>
  Sustainability<br>News<br>Careers<br>Testimonials<br>Warranty<br>Registration
</div>
<div class="col abs" style="left:753px">
  <h3>Contact Us</h3>
</div>
<div class="social abs">
  <span style="background:#3b5a99"></span>
  <span style="background:#c8232c"></span>
  <span style="background:#2aa3dd"></span>
  <span style="background:#c4302b"></span>
</div>
<div class="footer-phone abs">555-014-2290</div>
<div class="search abs">Search
  <svg width="14" height="14" viewBox="0 0 14 14" aria-hidden="true"><circle cx="6" cy="6" r="4.5" fill="none" stroke="#555" stroke-width="1.6"/><path d="M9.3 9.3L13 13" stroke="#555" stroke-width="1.8"/></svg>
</div>

<p class="copyright abs">©2014 Tavron Security Services. All Rights Reserved</p>

</body>
</html>
```